New & Improved KIVORA Business Card

I would like a two sided business card one side dedicated to home automation (security camera installation, television & sound bar mounting (hidden wires optional) , sink installation, fireplace mounting, chandelier installation and one side dedicated to all electronic repairs, In ex: plume band repairs, computer, zTab, laptop repairs, Velofon's, Korvex and etc.. Using the colors on this flyer. The phone number &email I want on both sides is (555) 214-3907 & Tech@Kivora.help. SAME COLOR AS THE FLYER ATTACHED.

Target Market(s)

EVERYONE.

Contact Information for Business Card

I would like a two sided business card one side dedicated to home automation (security camera installation, television & sound bar mounting (hidden wires optional) , sink installation, fireplace mounting, chandelier installation and one side dedicated to all electronic repairs, In ex: plume band repairs, computer, zTab, laptop repairs, Velofon's, Korvex and etc.. Using the colors on this flyer. The phone number &email I want on both sides is (555) 214-3907 & Tech@Kivora.help

Requirements
Must have
• -TV MOUNTING
-HOME AUTOMATION
-SECURITY CAMERA INSTALLATION
-ALL ELECTRONIC REPAIRS
- (555) 214-3907
-Tech@Kivora.help
-SAME COLOR AS THE FLYER
Nice to have
• Same colors & concept as the flyer attached below.
Should not have
• DO NOT DO A DIFF COLOR I WANT SAME COLOR AS THE FLYER ATTACHED.

```html
<!DOCTYPE html>
<html lang="en">
<head>
<meta charset="utf-8">
<title>KIVORA Business Card</title>
<link rel="stylesheet" href="https://fonts.googleapis.com/css2?family=Montserrat:wght@500;600;800&display=swap">
<style>
  :root {
    --card-pink: #ec2690;
    --ink-white: #ffffff;
    --backdrop: #4b4b4d;
    --shadow: rgba(0, 0, 0, 0.35);
  }
  * { margin: 0; padding: 0; box-sizing: border-box; }
  html, body {
    width: 1200px;
    height: 1126px;
    overflow: hidden;
    background: var(--backdrop);
  }
  .canvas {
    position: relative;
    width: 1200px;
    height: 1126px;
    display: flex;
    flex-direction: column;
    align-items: center;
    justify-content: center;
    gap: 44px;
  }
  .card {
    width: 880px;
    height: 503px;
    background: var(--card-pink);
    color: var(--ink-white);
    box-shadow: 0 14px 30px var(--shadow);
    display: flex;
    flex-direction: column;
    align-items: center;
    justify-content: center;
    font-family: "Montserrat", Arial, sans-serif;
  }
  .brand-name {
    font-weight: 800;
    font-size: 92px;
    letter-spacing: 0.22em;
    margin-right: -0.22em;
    line-height: 1;
  }
  .card--services .brand-name { font-size: 78px; }
  .service-list {
    margin-top: 62px;
    list-style: none;
    text-align: center;
    font-weight: 500;
    font-size: 21px;
    letter-spacing: 0.09em;
    line-height: 1.75;
  }
  .service-list .divider { margin: 0 14px; }
  .contact-row {
    margin-top: 30px;
    display: flex;
    align-items: center;
    gap: 48px;
    font-weight: 600;
    font-size: 25px;
    letter-spacing: 0.08em;
  }
  .contact-item {
    display: flex;
    align-items: center;
    gap: 14px;
  }
  .contact-icon { width: 28px; height: 28px; fill: var(--ink-white); }
  .contact-icon--mail { width: 36px; }
</style>
</head>
<body>
<main class="canvas">
  <section class="card card--services">
    <h1 class="brand-name">KIVORA</h1>
    <ul class="service-list">
      <li>TV MOUNTING<span class="divider">|</span>SECURITY CAMERA INSTALLATION</li>
      <li>HOME AUTOMATION<span class="divider">|</span>ALL ELECTRONIC REPAIRS</li>
    </ul>
  </section>

  <section class="card card--contact">
    <h2 class="brand-name">KIVORA</h2>
    <div class="contact-row">
      <span class="contact-item">
        <svg class="contact-icon" viewBox="0 0 24 24" aria-hidden="true">
          <path d="M6.6 10.8a15.1 15.1 0 0 0 6.6 6.6l2.2-2.2a1 1 0 0 1 1-.25 11.4 11.4 0 0 0 3.6.57 1 1 0 0 1 1 1V20a1 1 0 0 1-1 1A17 17 0 0 1 3 4a1 1 0 0 1 1-1h3.5a1 1 0 0 1 1 1c0 1.25.2 2.45.57 3.57a1 1 0 0 1-.25 1z"/>
        </svg>
        (555) 214-3907
      </span>
      <span class="contact-item">
        <svg class="contact-icon contact-icon--mail" viewBox="0 0 32 24" aria-hidden="true">
          <path d="M1 3h30v18H1z M2.5 4.5 16 14 29.5 4.5" fill="var(--ink-white)"/>
          <path d="M2.5 4.5 16 14 29.5 4.5" fill="none" stroke="var(--card-pink)" stroke-width="2"/>
        </svg>
        Tech@Kivora.help
      </span>
    </div>
  </section>
</main>
</body>
</html>
```